Gymnastics and fitness web design

Valdrey Gymnastics and fitness centre is opening a new branch in the United States.
Target Audience:
22 to 40 year old people who are not satisfied with their current body figure, shape and size.
and
Our programs
VoltaRig, Sports performance and personal training
DESIGN STYLE:
We want the site to be trendy, edgy and cool. The colors we prefer are blue, black and silver. Th idea is people should get motivated by seeing our website. We don't like adding many text in the design, images oriented design is what we are after.
Contents should be added-
Slider
who we are?
section for our programs
Why us?
Video showing some tutorials
Articles
contact us form with map, Address, Phone number, timings, and social media buttons.

```html
<!DOCTYPE html>
<html lang="en">
<head>
<meta charset="utf-8">
<title>Valdrey — Why Choose Us</title>
<link rel="stylesheet" href="https://fonts.googleapis.com/css2?family=Antonio:wght@400;500&family=Open+Sans:wght@400&display=swap">
<style>
  :root {
    --panel-dark: #333333;
    --page-white: #ffffff;
    --card-border: #e4e4e4;
    --rule-light: #ececec;
    --accent-green: #9bbb2e;
    --icon-grey: #d6d6d6;
    --rule-grey: #cfcfcf;
    --ink-dark: #222222;
    --ink-body: #3a3a3a;
    --ink-light: #ffffff;
    --strip-warm: #b9a88d;
    --strip-cool: #1f3f86;
  }
  * { box-sizing: border-box; margin: 0; padding: 0; }
  html, body { width: 1200px; height: 528px; overflow: hidden; background: var(--page-white); }
  .canvas { position: relative; width: 1200px; height: 528px; overflow: hidden; background: var(--page-white); }

  .photo-strip { position: absolute; top: 0; height: 2px; }
  .photo-strip--left { left: 70px; width: 516px; background: linear-gradient(90deg, var(--strip-warm), #d9d2c4); }
  .photo-strip--right { left: 601px; width: 525px; background: linear-gradient(90deg, #d64a3a, var(--strip-cool) 40%, #e8d7b0 80%, #8a5a3a); }
  .section-rule { position: absolute; top: 30px; left: 0; width: 1200px; height: 1px; background: var(--rule-light); }

  .intro-panel {
    position: absolute; left: 0; top: 30px; width: 489px; height: 498px;
    background: var(--panel-dark); color: var(--ink-light);
  }
  .intro-title {
    position: absolute; left: 73px; top: 40px;
    font-family: "Antonio", sans-serif; font-weight: 400; font-size: 38px; line-height: 1;
  }
  .intro-subtitle {
    position: absolute; left: 73px; top: 136px;
    font-family: "Antonio", sans-serif; font-weight: 400; font-size: 19px; line-height: 1;
  }
  .intro-text {
    position: absolute; left: 73px; top: 166px; width: 300px;
    font-family: "Open Sans", sans-serif; font-size: 12.8px; line-height: 18.4px;
  }
  .intro-rule { position: absolute; left: 75px; top: 369px; width: 104px; height: 2px; background: var(--accent-green); }
  .team-button {
    position: absolute; left: 74px; top: 399px; width: 170px; height: 34px;
    border: 1px solid var(--ink-light); color: var(--ink-light);
    font-family: "Open Sans", sans-serif; font-size: 13px; line-height: 32px; text-align: center;
  }

  .steps-card {
    position: absolute; left: 400px; top: 73px; width: 726px; height: 412px;
    background: var(--page-white); border: 1px solid var(--card-border);
  }
  .step { position: absolute; width: 260px; }
  .step--visit { left: 62px; top: 36px; }
  .step--contact { left: 384px; top: 36px; }
  .step--advice { left: 62px; top: 228px; }
  .step--pro { left: 384px; top: 228px; }
  .step-icon { display: block; width: 50px; height: 50px; }
  .step-title {
    margin-top: 10px;
    font-family: "Antonio", sans-serif; font-weight: 400; font-size: 19px; line-height: 22px; color: var(--ink-dark);
  }
  .step-rule { margin-top: 4px; width: 28px; height: 2px; background: var(--rule-grey); }
  .step--active .step-rule { width: 256px; height: 3px; background: var(--accent-green); }
  .step-text {
    margin-top: 12px; width: 245px;
    font-family: "Open Sans", sans-serif; font-size: 12.8px; line-height: 18.4px; color: var(--ink-body);
  }
  .step--active .step-text { margin-top: 11px; }
</style>
</head>
<body>
<main class="canvas">
  <div class="photo-strip photo-strip--left" role="img" aria-label="Bottom edge of a gym photograph"></div>
  <div class="photo-strip photo-strip--right" role="img" aria-label="Bottom edge of a training photograph"></div>
  <div class="section-rule"></div>

  <section class="intro-panel">
    <h2 class="intro-title">Why Choose Us</h2>
    <h3 class="intro-subtitle">Following 4 simple steps</h3>
    <p class="intro-text">Lorem ipsum dolor sit amet, consectetur adipisicing elit, sed do eiusmod tempor incididunt ut labore et dolore magna aliqua. Ut enim ad minim veniam, quis nostrud exercitation ullamco laboris nisi ut aliquip ex ea commodo consequat. Duis aute irure dolor in reprehenderit in voluptate velit esse cillum</p>
    <div class="intro-rule"></div>
    <a class="team-button">About Harlowe Team</a>
  </section>

  <section class="steps-card">
    <article class="step step--visit step--active">
      <svg class="step-icon" viewBox="0 0 50 50" aria-hidden="true">
        <circle cx="21" cy="21" r="17" fill="none" stroke="#9bbb2e" stroke-width="4"/>
        <line x1="33" y1="33" x2="46" y2="46" stroke="#9bbb2e" stroke-width="5" stroke-linecap="round"/>
        <circle cx="21" cy="16" r="5.5" fill="#9bbb2e"/>
        <path d="M11 30 Q12 22 21 22 Q30 22 31 30 Z" fill="#9bbb2e"/>
      </svg>
      <h4 class="step-title">Visit Us</h4>
      <div class="step-rule"></div>
      <p class="step-text">Start by Meeting Our Professionals.</p>
    </article>

    <article class="step step--contact">
      <svg class="step-icon" viewBox="0 0 50 50" aria-hidden="true">
        <circle cx="24" cy="24" r="21" fill="none" stroke="#d6d6d6" stroke-width="3"/>
        <path d="M15 13 L20 11 L23 18 L19 21 Q22 27 27 30 L30 26 L37 29 L35 34 Q31 38 24 33 Q15 27 13 19 Q12 15 15 13 Z" fill="#d6d6d6"/>
        <path d="M27 12 Q35 14 37 22" fill="none" stroke="#d6d6d6" stroke-width="2"/>
        <path d="M27 17 Q31 18 32 22" fill="none" stroke="#d6d6d6" stroke-width="2"/>
      </svg>
      <h4 class="step-title">Call / Email</h4>
      <div class="step-rule"></div>
      <p class="step-text">Call or email members to have your requirements fulfilled.</p>
    </article>

    <article class="step step--advice">
      <svg class="step-icon" viewBox="0 0 90 50" aria-hidden="true" style="width:86px">
        <path d="M2 14 H14 Q13 6 20 6 Q27 6 26 14 H38 V24 Q46 23 46 30 Q46 37 38 36 V46 H2 Z" fill="#d6d6d6"/>
        <path d="M44 20 L56 14 Q55 7 62 6 Q68 6 68 13 L80 16 L77 27 Q84 28 83 34 Q82 40 75 38 L72 48 L58 44 L56 32 Q50 34 48 29 Z" fill="#d6d6d6"/>
      </svg>
      <h4 class="step-title">Start from professionals</h4>
      <div class="step-rule"></div>
      <p class="step-text">Hear advice from a gymnastic professional and decide what is best for your fitness.</p>
    </article>

    <article class="step step--pro">
      <svg class="step-icon" viewBox="0 0 50 50" aria-hidden="true">
        <circle cx="25" cy="6" r="5" fill="#d6d6d6"/>
        <path d="M18 13 H32 V30 H28 V44 H22 V30 H18 Z" fill="#d6d6d6"/>
        <ellipse cx="25" cy="40" rx="20" ry="7" fill="none" stroke="#d6d6d6" stroke-width="3"/>
      </svg>
      <h4 class="step-title">Do it like A Pro</h4>
      <div class="step-rule"></div>
      <p class="step-text">Hire who you like and take control of your Daily Classes</p>
    </article>
  </section>
</main>
</body>
</html>
```